Steadfast Field Crews

We are a underground coal mining labour hire company, needing a website that links into our online payroll (www.wagelinkr.com.au) and also need to have job applications page that is a preform with drop down menu,s with answers or check boxes. We would also need a 3 tier administration access for access to different files.
We are looking for an ongoing relationship with future app integration

Reason: There are a few more designs to come and I'm out at the mine for another week

Industry/Entity Type

Coal Mining

```html
<!DOCTYPE html>
<html lang="en">
<head>
<meta charset="utf-8">
<title>Steadfast Field Crews</title>
<link href="https://fonts.googleapis.com/css2?family=Open+Sans:wght@400;600&display=swap" rel="stylesheet">
<style>
:root{
  --black:#050505;
  --orange:#f0a04a;
  --orange-deep:#c8641c;
  --orange-btn:#f08a2a;
  --text:#555;
  --grey-band:#e6e6e6;
  --footer:#efefef;
  --rule:#cfcfcf;
  --panel:#1c1a19;
  --navy:#3a4aa0;
}
*{box-sizing:border-box;margin:0;padding:0}
html,body{width:1150px;height:1200px;overflow:hidden}
body{font-family:"Open Sans",Arial,sans-serif;background:#fff;position:relative;color:var(--text)}
.abs{position:absolute}
.site-header{position:absolute;left:0;top:0;width:1150px;height:227px;background:var(--black)}
.brand{position:absolute;left:95px;top:80px;display:flex;align-items:center;gap:10px}
.brand-dot{width:34px;height:34px;border-radius:50%;background:var(--orange-btn)}
.brand-name{color:var(--orange);font-size:19px;font-weight:600;line-height:1.2;width:140px}
.call{position:absolute;right:95px;top:46px;display:flex;align-items:center;gap:10px;text-align:right}
.call-label{color:#ddd;font-size:18px;line-height:22px}
.call-number{color:var(--orange);font-size:22px;line-height:26px}
.main-nav{position:absolute;left:367px;top:167px;width:688px;height:30px;border-bottom:3px solid #3a3a3a;display:flex}
.main-nav a{color:#eee;font-size:13px;text-decoration:none;height:30px;padding:0 7px;margin-right:13px;position:relative}
.main-nav a:last-child{margin-right:0;padding-right:5px}
.main-nav a.active{color:var(--orange-btn)}
.main-nav a.active::after{content:"";position:absolute;left:0;right:0;bottom:-3px;height:3px;background:var(--orange-btn)}
.hero-band{position:absolute;left:0;top:229px;width:1150px;height:409px;background:var(--grey-band)}
.hero-photo{position:absolute;left:95px;top:235px;width:704px;height:395px;background:linear-gradient(135deg,#6b4538 0%,#a2603f 35%,#7a4a3a 55%,#b56a44 80%,#8a5a48 100%)}
.hero-caption{position:absolute;left:799px;top:235px;width:256px;height:395px;background:linear-gradient(180deg,#1e1a18,#2a2523);padding:97px 27px 0}
.hero-caption h2{color:var(--orange);font-size:18px;font-weight:400;line-height:26px}
.hero-caption p{color:#ddd;font-size:13px;line-height:20px;margin-top:13px}
.btn-apply{display:inline-block;margin-top:17px;background:#fff;color:#222;font-size:13px;padding:10px 12px;border-radius:2px}
.dots{display:flex;gap:8px;margin-top:28px}
.dots span{width:14px;height:14px;border-radius:50%;background:#999;border:1px solid #666}
.dots span:first-child{background:#555}
.welcome{position:absolute;left:97px;top:666px;width:674px}
.section-title{color:var(--orange-deep);font-size:22px;font-weight:400;line-height:30px}
.welcome p{font-size:13px;line-height:22px;margin-top:8px}
.welcome p:first-of-type{margin-top:14px}
.divider{position:absolute;left:95px;top:880px;width:676px;height:1px;background:var(--rule)}
.mission-photo{position:absolute;left:95px;top:899px;width:228px;height:135px;background:linear-gradient(160deg,#4a3a28,#8a7a3a 50%,#c9a92a 65%,#3a3228)}
.mission{position:absolute;left:338px;top:893px;width:430px}
.mission p{font-size:13px;line-height:20px;margin-top:6px}
.more{display:block;color:var(--orange-deep);font-size:12px;margin-top:7px;text-decoration:none}
.promo{position:absolute;left:798px;top:672px;width:257px;height:362px;background:#000}
.promo-photo{height:174px;background:linear-gradient(180deg,#4a6a9a 0%,#8aa0c0 60%,#22252a 100%)}
.promo p{color:var(--orange);font-size:14px;line-height:21px;padding:22px 27px 0}
.btn-download{position:absolute;left:22px;top:292px;display:flex;align-items:center}
.pdf-box{width:34px;height:42px;background:#eee;border-radius:2px;position:relative;z-index:1}
.download-label{background:var(--orange-btn);color:#fff;font-size:15px;font-weight:600;padding:8px 12px 8px 14px;margin-left:-4px;border-radius:2px;letter-spacing:.3px}
.site-footer{position:absolute;left:0;top:1063px;width:1150px;height:137px;background:var(--footer);border-top:1px solid #ddd}
.footer-nav{position:absolute;left:96px;top:22px;font-size:13px;color:#666}
.footer-nav a{color:#666;text-decoration:none}
.footer-nav .sep{margin:0 12px}
.copyright{position:absolute;left:96px;top:54px;font-size:13px;color:#666}
.social{position:absolute;left:96px;top:90px;display:flex;gap:6px}
.social span{width:24px;height:24px;border-radius:3px}
.social .s1{background:#3b5a9a}
.social .s2{background:#4ab0e0}
.payroll{position:absolute;right:96px;top:30px;display:flex;align-items:center;gap:8px}
.payroll-mark{width:30px;height:30px;background:var(--navy);border-radius:4px}
.payroll-name{color:#555;font-size:28px;font-weight:400;line-height:1}
</style>
</head>
<body>
<header class="site-header">
  <div class="brand"><span class="brand-dot"></span><span class="brand-name">Steadfast Field Crews</span></div>
  <div class="call">
    <div><div class="call-label">Call us</div><div class="call-number">655 318 4027</div></div>
    <svg width="30" height="30" viewBox="0 0 24 24" aria-hidden="true"><path fill="#aaa" d="M6.6 10.8c1.4 2.8 3.8 5.1 6.6 6.6l2.2-2.2c.3-.3.7-.4 1-.2 1.1.4 2.3.6 3.6.6.6 0 1 .4 1 1V20c0 .6-.4 1-1 1C10.6 21 3 13.4 3 4c0-.6.4-1 1-1h3.5c.6 0 1 .4 1 1 0 1.3.2 2.5.6 3.6.1.3 0 .7-.2 1l-2.3 2.2z"/></svg>
  </div>
  <nav class="main-nav">
    <a class="active" href="#">HOME</a><a href="#">APPLY FOR POSITION</a><a href="#">PAY PORTAL</a><a href="#">DOWNLOAD</a><a href="#">MISSION</a><a href="#">ABOUT US</a><a href="#">CONTACT US</a>
  </nav>
</header>

<div class="hero-band"></div>
<div class="hero-photo" role="img" aria-label="Aerial view of a terraced open-cut mine with red earth"></div>
<div class="hero-caption">
  <h2>Excepteur sint occaecat cupidatat proident</h2>
  <p>Suspendisse ullamcorper ante a tellus auctor, eu aliquet justo vul­putate. Mauris dictum posuere.</p>
  <span class="btn-apply">APPLY FOR JOBS</span>
  <div class="dots"><span></span><span></span><span></span><span></span></div>
</div>

<section class="welcome">
  <h1 class="section-title">Welcome to Steadfast Field Crews</h1>
  <p>We are KRMB pty ltd trading as Steadfast Field Crews, we are experienced in ground consolidation in underground coal mines, in short when they collapse or cave in we come in with chemical pumps and stabilise the ground or fill cavities which will then allow for the mining process to continue. We also do general mine labor as well.</p>
  <p>We are a labor hire company for major mining services company, we offer labor solutions in New South Wales and Queensland in the underground coal mines.</p>
</section>
<div class="divider"></div>
<div class="mission-photo" role="img" aria-label="Underground coal mining machine in a tunnel"></div>
<section class="mission">
  <h2 class="section-title">Our Mission</h2>
  <p>Donec quis pellentesque dui. Proin viverra velit volutpat posuere dictum. Aliquam justo tellus, varius a feugiat eget, rhoncus vitae dolor. Nullam tempus laoreet tortor, a porta dui vehicula quis. Duis porta neque mi, non volutpat nulla interdum ut.</p>
  <a class="more" href="#">VIEW MORE</a>
</section>

<aside class="promo">
  <div class="promo-photo" role="img" aria-label="Silhouettes of two miners beside a mine vehicle against the sky"></div>
  <p>Nulla lobortis dapibus gravida. Fusce iaculis adipiscing aliquet. Quisque sed consequat lorem, ac tincidunt nisi.</p>
  <div class="btn-download"><span class="pdf-box"></span><span class="download-label">DOWNLOAD</span></div>
</aside>

<footer class="site-footer">
  <div class="footer-nav"><a href="#">Home</a><span class="sep">|</span><a href="#">Apply for position</a><span class="sep">|</span><a href="#">Pay Portal</a><span class="sep">|</span><a href="#">Download</a><span class="sep">|</span><a href="#">Mission</a><span class="sep">|</span><a href="#">About us</a><span class="sep">|</span><a href="#">Contact us</a></div>
  <div class="copyright">Copyright &copy; 2014 &nbsp;Steadfast Field Crews. &nbsp;All rights reserved.</div>
  <div class="social"><span class="s1"></span><span class="s2"></span></div>
  <div class="payroll"><span class="payroll-mark"></span><span class="payroll-name">wagelinkr</span></div>
</footer>
</body>
</html>
```